Looking for a modern, Professional business card design

We have a simple business card, but are looking for a more modern, professional look. A sample of the basic card is attached as well as the logo. We would also like to add that we offer:
Struggling with your finances?
- Learn to become debt free
- Discover the power of cash
- Control your money instead of it controlling you
Let us help you achieve a new level of financial freedom!
Also, we would like to have a "SPECIAL OFFER!: FREE 30 minute consultation"
Financial Planning

```html
<!DOCTYPE html>
<html lang="en">
<head>
<meta charset="utf-8">
<title>Summit Financial Coaching – Business Card</title>
<link rel="stylesheet" href="https://fonts.googleapis.com/css2?family=PT+Sans:ital,wght@0,400;0,700;1,400&display=swap">
<style>
  :root {
    --backdrop: #4a4a4a;
    --paper: #ffffff;
    --ink: #1e1e1e;
    --ink-soft: #444444;
    --green: #4f9a2e;
    --green-deep: #3a8f3c;
    --lime: #a6d13a;
    --black: #000000;
    --white: #ffffff;
  }
  * { box-sizing: border-box; margin: 0; padding: 0; }
  html, body {
    width: 1105px; height: 1200px; overflow: hidden;
    background: var(--backdrop);
    font-family: "PT Sans", Arial, sans-serif;
  }
  .card {
    position: absolute; left: 192px; width: 720px; height: 413px; overflow: hidden;
  }
  /* Front */
  .card-front { top: 181px; background: var(--paper); }
  .brand-lockup {
    position: absolute; left: 41px; top: 50px;
    display: flex; align-items: center; gap: 14px;
  }
  .brand-dot { width: 30px; height: 30px; border-radius: 50%; background: var(--green); }
  .brand-name {
    color: var(--green); font-weight: 700; font-size: 31px; letter-spacing: 0.5px;
  }
  .holder { position: absolute; right: 53px; top: 182px; text-align: right; }
  .holder-name { color: var(--green); font-size: 25px; line-height: 1.2; }
  .holder-title { color: var(--ink); font-size: 20px; line-height: 1.3; }
  .contact-list { position: absolute; left: 48px; top: 268px; list-style: none; }
  .contact-item {
    display: flex; align-items: center; gap: 10px;
    color: var(--ink-soft); font-size: 19px; line-height: 27.5px;
  }
  .contact-icon { width: 17px; height: 17px; flex: none; }
  .card-band {
    position: absolute; left: 0; bottom: 0; width: 100%; height: 27px;
    background: linear-gradient(90deg, var(--green-deep) 0%, var(--green) 30%, var(--lime) 62%, var(--lime) 84%, var(--black) 84%);
  }
  /* Back */
  .card-back {
    top: 636px;
    background: radial-gradient(ellipse 520px 340px at 386px 192px, var(--lime) 0%, #7cbf3a 40%, var(--green-deep) 100%);
    color: var(--white);
  }
  .pitch { position: absolute; right: 23px; top: 52px; text-align: right; }
  .pitch-heading { font-weight: 700; font-size: 19px; line-height: 1.3; margin-bottom: 2px; }
  .pitch-list { list-style: none; }
  .pitch-item {
    font-style: italic; font-size: 18px; line-height: 25px;
    display: flex; justify-content: flex-end; align-items: center; gap: 12px;
  }
  .pitch-item::after {
    content: ""; width: 8px; height: 8px; border-radius: 50%; background: var(--white);
  }
  .pitch-closing { font-style: italic; font-size: 18px; line-height: 25px; }
  .offer { position: absolute; right: 41px; top: 196px; text-align: right; }
  .offer-title { font-weight: 700; font-size: 24px; line-height: 1.2; }
  .offer-detail { font-weight: 700; font-size: 17px; line-height: 1.3; }
  .back-brand {
    position: absolute; right: 41px; top: 268px; text-align: right;
    font-weight: 700; color: var(--white); line-height: 1;
  }
  .back-brand-main { display: block; font-size: 62px; letter-spacing: 1px; }
  .back-brand-sub { display: block; font-size: 25px; margin-top: 6px; }
</style>
</head>
<body>

<section class="card card-front" aria-label="Card front">
  <div class="brand-lockup">
    <span class="brand-dot"></span>
    <span class="brand-name">SUMMIT FINANCIAL COACHING</span>
  </div>

  <div class="holder">
    <p class="holder-name">Daniel R. Hayes</p>
    <p class="holder-title">Personal Financial Coach</p>
  </div>

  <ul class="contact-list">
    <li class="contact-item">
      <svg class="contact-icon" viewBox="0 0 16 16" aria-hidden="true">
        <rect x="4" y="1" width="8" height="14" rx="1.5" fill="#4f9a2e"/>
        <rect x="5.3" y="3" width="5.4" height="8.5" fill="#fff"/>
        <circle cx="8" cy="13.2" r="0.8" fill="#fff"/>
      </svg>
      (555) 014-2287
    </li>
    <li class="contact-item">
      <svg class="contact-icon" viewBox="0 0 16 16" aria-hidden="true">
        <rect x="1" y="3.5" width="14" height="9" fill="#4f9a2e"/>
        <path d="M1.5 4 L8 9 L14.5 4" fill="none" stroke="#fff" stroke-width="1.2"/>
      </svg>
      daniel@steadywalletcoaching.com
    </li>
    <li class="contact-item">
      <svg class="contact-icon" viewBox="0 0 16 16" aria-hidden="true">
        <circle cx="8" cy="8" r="7" fill="#4f9a2e"/>
        <path d="M4 5 Q6 4 7 6 Q6 8 4.5 8 Z M9 9 Q11 8 12 10 Q11 12.5 9.5 12 Z M9 3 Q11 3 12 5 L10 5.5 Z" fill="#fff"/>
      </svg>
      www.steadywalletcoaching.com
    </li>
  </ul>

  <div class="card-band"></div>
</section>

<section class="card card-back" aria-label="Card back">
  <div class="pitch">
    <p class="pitch-heading">STRUGGLING WITH YOUR FINANCES?</p>
    <ul class="pitch-list">
      <li class="pitch-item">Learn to become debt free</li>
      <li class="pitch-item">Discover the power of cash</li>
      <li class="pitch-item">Control your money instead of it controlling you</li>
    </ul>
    <p class="pitch-closing">Let us help you achieve a new level of financial freedom!</p>
  </div>

  <div class="offer">
    <p class="offer-title">SPECIAL OFFER!</p>
    <p class="offer-detail">FREE 30 minute consultation</p>
  </div>

  <p class="back-brand">
    <span class="back-brand-main">SUMMIT</span>
    <span class="back-brand-sub">FINANCIAL COACHING</span>
  </p>
</section>

</body>
</html>
```